Hello my name is Colin, I am Starting a business called Lumen Wellness and fitness and am in need of a memorable business card.
It is a personal training studio. I have added the logo that i would like to be on the left center om my business card. i would like room left up the top for a heading sentence such as. "Is your body shocking for all the wrong reasons". there must be room left on the right of the logo below the main heading for 3 sub headings.
then under those 3 headings and logo room for another larger heading eg. "give me a call and learn how to eat chocolate, drink bear and have great sex". in what room is left i would like to be used for my contact details, use I'm Colin Ferrante your fitness expert on the left then on the right Phone, Email and website space in at least 12 Point. Very specific i know :) now onto the back, for the back i would like an eye catching graphic and room for one main headline and 3 bullet points centered just write anything i will choose what to put in them when i pick a winner. Thank you very much for sticking through all of that :) i appreciate you taking the time to read it and hopefully undergo designing me a business card.
I can't wait to see the designs!

Target Market(s)

slightly more towards females although it would probably be best if it was targeted towards both sexes

Industry/Entity Type

Training

Requirements
Nice to have
• I would love to see if anyone could come up with a design that would really make my card stand out and be memorable.
Should not have
• tacky fitness photos of abs and muscles etc.

```html
<!DOCTYPE html>
<html lang="en">
<head>
<meta charset="utf-8">
<title>Lumen Wellness and fitness – Business Card</title>
<link href="https://fonts.googleapis.com/css2?family=Questrial&family=Montserrat:wght@600;700&display=swap" rel="stylesheet">
<style>
  :root {
    --navy: #123e73;
    --navy-deep: #0b2a52;
    --navy-mid: #1d4f8c;
    --white: #ffffff;
    --grey-text: #555b63;
    --soft-grey: #d9dce0;
    --stage: #eceef1;
  }
  * { margin: 0; padding: 0; box-sizing: border-box; }
  html, body { width: 1200px; height: 1024px; overflow: hidden; background: var(--stage); }
  .stage {
    position: relative; width: 1200px; height: 1024px;
    display: flex; flex-direction: column; align-items: center; gap: 44px; padding-top: 60px;
  }
  .card {
    position: relative; width: 770px; height: 440px; overflow: hidden;
    box-shadow: 0 6px 18px rgba(0,0,0,.18);
  }
  /* ---------- front ---------- */
  .card-front { background: var(--white); }
  .front-visual {
    position: absolute; right: 0; top: 0; width: 430px; height: 190px;
    background: radial-gradient(ellipse at 55% 45%, #cfd3d8 0%, #eef0f2 55%, var(--white) 80%);
    opacity: .8;
  }
  .front-wave { position: absolute; left: 0; bottom: 0; width: 770px; height: 120px; }
  .wordmark { position: absolute; left: 48px; top: 96px; font-family: "Questrial", sans-serif; color: var(--navy); }
  .wordmark-name { display: flex; align-items: center; gap: 12px; font-size: 84px; line-height: 1; }
  .wordmark-dot { width: 22px; height: 22px; background: var(--navy); border-radius: 50%; }
  .wordmark-tag { font-size: 19px; color: var(--grey-text); margin: 6px 0 0 4px; }
  .headline-band {
    position: absolute; left: 0; top: 232px; width: 100%; background: var(--navy);
    color: var(--white); font-family: "Montserrat", sans-serif; padding: 9px 0 9px 48px;
    white-space: nowrap;
  }
  .headline-main { font-size: 19px; line-height: 24px; font-weight: 700; letter-spacing: .4px; text-transform: uppercase; }
  .headline-sub { font-size: 11.5px; line-height: 16px; font-weight: 600; letter-spacing: .3px; text-transform: uppercase; margin-top: 2px; }
  .trainer { position: absolute; right: 48px; top: 168px; text-align: right; font-family: "Montserrat", sans-serif; }
  .trainer-name { font-size: 20px; font-weight: 700; color: var(--navy); }
  .trainer-role { font-family: "Questrial", sans-serif; font-size: 15px; color: var(--grey-text); }
  .contacts { position: absolute; left: 48px; top: 312px; list-style: none; font-family: "Questrial", sans-serif; font-size: 19px; color: var(--grey-text); }
  .contacts li { display: flex; align-items: center; gap: 10px; line-height: 26px; }
  .contacts svg { width: 14px; height: 14px; fill: var(--navy); }
  /* ---------- back ---------- */
  .card-back { background: linear-gradient(160deg, var(--navy-mid) 0%, var(--navy) 45%, var(--navy-deep) 100%); color: var(--white); }
  .back-visual {
    position: absolute; left: 0; top: 0; width: 100%; height: 200px;
    background: radial-gradient(ellipse at 40% 40%, rgba(80,130,195,.55) 0%, rgba(40,90,160,.2) 50%, rgba(0,0,0,0) 75%);
  }
  .back-gloss { position: absolute; left: 0; top: 0; width: 100%; height: 100%; background: linear-gradient(120deg, rgba(255,255,255,.08) 0%, rgba(255,255,255,0) 40%); }
  .back-wordmark { position: absolute; left: 0; right: 0; top: 210px; text-align: center; font-family: "Questrial", sans-serif; }
  .back-wordmark .wordmark-name { justify-content: center; font-size: 96px; color: var(--white); }
  .back-wordmark .wordmark-dot { background: var(--white); }
  .back-wordmark .wordmark-tag { color: var(--white); font-size: 21px; margin: 6px 0 0; }
  .back-web { font-size: 15px; letter-spacing: .5px; margin-top: 4px; }
</style>
</head>
<body>
<main class="stage">
  <section class="card card-front" aria-label="Business card front">
    <div class="front-visual" role="img" aria-label="Faint grey photo of people training together"></div>
    <svg class="front-wave" viewBox="0 0 770 120" preserveAspectRatio="none" aria-hidden="true">
      <path d="M0 120 L0 100 C240 110 480 80 770 20 L770 120 Z" fill="var(--navy)"/>
      <path d="M0 100 C240 110 480 80 770 20 L770 34 C480 92 240 116 0 108 Z" fill="var(--navy-mid)"/>
    </svg>
    <div class="wordmark">
      <div class="wordmark-name"><span>Lumen</span><span class="wordmark-dot"></span></div>
      <div class="wordmark-tag">Wellness and fitness</div>
    </div>
    <div class="trainer">
      <div class="trainer-name">Colin Ferrante</div>
      <div class="trainer-role">fitness expert</div>
    </div>
    <div class="headline-band">
      <div class="headline-main">Is your body shocking for all the wrong reasons</div>
      <div class="headline-sub">Give me a call and learn how to eat chocolate drink bear and have great sex</div>
    </div>
    <ul class="contacts">
      <li><svg viewBox="0 0 16 16"><path d="M3 1h3l1.5 4-2 1.5a9 9 0 0 0 4 4l1.5-2 4 1.5v3c0 1-1 2-2 2A13 13 0 0 1 1 3c0-1 1-2 2-2z"/></svg>000-000-000</li>
      <li><svg viewBox="0 0 16 16"><path d="M1 3h14v10H1z M1 3l7 6 7-6" stroke="var(--white)" stroke-width="1"/></svg>hello@lumenwellness.com</li>
      <li><svg viewBox="0 0 16 16"><circle cx="8" cy="8" r="7"/><path d="M1 8h14M8 1c3 3 3 11 0 14M8 1c-3 3-3 11 0 14" stroke="var(--white)" stroke-width="1" fill="none"/></svg>www.lumenwellness.com</li>
    </ul>
  </section>

  <section class="card card-back" aria-label="Business card back">
    <div class="back-visual" role="img" aria-label="Faint blue photo of hands reaching during training"></div>
    <div class="back-gloss"></div>
    <div class="back-wordmark">
      <div class="wordmark-name"><span>Lumen</span><span class="wordmark-dot"></span></div>
      <div class="wordmark-tag">Wellness and fitness</div>
      <div class="back-web">www.lumenwellness.com</div>
    </div>
  </section>
</main>
</body>
</html>
```